Business Card Design needed for start up company Halvora

In need of a new business card designed for a start up company based in Sydney, Halvora is a new start up innovative Company, our mission it to make property accessible for everyday Australian and to become the leading Real Estate platform in Australia. We want it to be fresh and clean.

Industry/Entity Type

Financial

Contact Information for Business Card

Section for Name
Section for Title

HALVORA - The Strength of Pooling
Mobile:
Direct:

Font styles to use
Sans Serif

Colors
33a6d7
0692cd
0255a3
ffffff

Requirements
Must have
• Logo, all business card details

```html
<!DOCTYPE html>
<html lang="en">
<head>
<meta charset="utf-8">
<title>Halvora – Business Card</title>
<link rel="stylesheet" href="https://fonts.googleapis.com/css2?family=Open+Sans:wght@400;600;700;800&display=swap">
<style>
  :root{
    --backdrop:#939393;
    --card-white:#ffffff;
    --sky:#2a9ed8;
    --sky-bright:#33a6d7;
    --navy:#1d3f7c;
    --navy-deep:#1b3a72;
    --navy-card:#21437f;
    --ink:#3a3a3a;
    --rule:#5f7fb3;
  }
  *{margin:0;padding:0;box-sizing:border-box}
  html,body{width:1200px;height:900px;overflow:hidden}
  body{background:var(--backdrop);font-family:"Open Sans",Arial,sans-serif;position:relative}

  .card{position:absolute;top:306px;width:439px;height:271px;border-radius:12px;overflow:hidden}
  .card--front{left:149px;background:var(--card-white)}
  .card--back{left:608px;background:linear-gradient(180deg,#23467f 0%,var(--navy-card) 60%,#1f3f78 100%)}

  /* front: brand block */
  .brand-mark{position:absolute;left:87px;top:77px;width:64px;height:64px;border-radius:50%;background:var(--sky)}
  .brand-name{position:absolute;left:0;width:239px;top:152px;text-align:center;
    font-weight:800;font-size:36px;letter-spacing:-0.5px;color:var(--navy);line-height:44px}
  .divider{position:absolute;left:217px;top:77px;width:2px;height:120px;background:var(--rule)}

  /* front: contact block */
  .person{position:absolute;left:245px;top:74px}
  .person__name{font-weight:700;font-size:15.5px;letter-spacing:0.2px;color:var(--navy);line-height:20px}
  .person__first{color:var(--sky)}
  .person__title{font-size:12px;color:var(--ink);line-height:15px}
  .contacts{position:absolute;left:244px;top:133px;list-style:none}
  .contacts li{display:flex;align-items:center;height:16px;font-size:12px;color:var(--ink)}
  .contacts svg{width:10px;height:10px;margin-right:6px;fill:var(--navy)}

  /* back */
  .back-texture{position:absolute;inset:0}
  .back-brand{position:absolute;left:0;right:0;top:105px;display:flex;align-items:center;justify-content:center;gap:10px}
  .back-brand__mark{width:62px;height:62px;border-radius:50%;background:var(--card-white)}
  .back-brand__name{font-weight:800;font-size:42px;letter-spacing:-0.5px;color:var(--card-white);line-height:50px}
  .tagline{position:absolute;left:0;right:0;top:184px;text-align:center;
    font-weight:700;font-size:12.5px;color:var(--card-white);letter-spacing:0.1px}
</style>
</head>
<body>
  <section class="card card--front" aria-label="Business card front">
    <div class="brand-mark"></div>
    <div class="brand-name">HALVORA</div>
    <div class="divider"></div>

    <div class="person">
      <p class="person__name"><span class="person__first">MARCUS</span> REID</p>
      <p class="person__title">Managing Director</p>
    </div>

    <ul class="contacts">
      <li><svg viewBox="0 0 10 10"><path d="M1 3.2C1 2 2.5 1.2 5 1.2S9 2 9 3.2V4H7V3H3v1H1z M2.2 4.6h5.6L9 8.8H1z"/></svg>044-555 010 234</li>
      <li><svg viewBox="0 0 10 10"><path d="M3 0.5h4a0.8 0.8 0 0 1 .8.8v7.4a.8.8 0 0 1-.8.8H3a.8.8 0 0 1-.8-.8V1.3A.8.8 0 0 1 3 .5zM3.2 1.6v6h3.6v-6z"/></svg>044-555 010 234</li>
      <li><svg viewBox="0 0 10 10"><path d="M0.5 2h9v6h-9z M1 2.4 5 5.6 9 2.4" stroke="#fff" stroke-width=".8"/></svg>hello@halvora.com</li>
      <li><svg viewBox="0 0 10 10"><circle cx="5" cy="5" r="4.5"/><path d="M3 3.5l2 1-1 2.5M6 2.5l1.5 2-1.5 2.5" stroke="#fff" stroke-width=".7" fill="none"/></svg>www.halvora.com</li>
    </ul>
  </section>

  <section class="card card--back" aria-label="Business card back">
    <div class="back-texture" role="img" aria-label="Subtle embossed repeating brand-symbol texture across the navy background"></div>
    <div class="back-brand">
      <div class="back-brand__mark"></div>
      <div class="back-brand__name">HALVORA</div>
    </div>
    <p class="tagline">THE STRENGTH OF POOLING</p>
  </section>
</body>
</html>
```